Website for Dental Office - The Bright Arch Clinic

The bright arch clinic is a dental office offering cosmetic dentistry, general dentistry, and multi-specialty dental care all under one roof in our state-of-the-art cosmetic dental center. We are particularly striving to provide services that fit the need of the young generation. Thus, we hope to have a modern, professional concise website that represents our spirit.

*Should be able to switch from English to Chinese

6 sections besides homepage:
Home, Meet us, Services,
Patient Info, Cases&Reviews, Blog, Contact

The Services sections should contain multiple subsections such as cleaning and prevention, cosmetic dentistry, implant dentistry, removable dentures, etc...
The Patient Info section is also intended to contain several subsections such as
New Patient offer, accepted Insurance, patient portal, helpful tips, etc...

Target Market(s)

young generation

Coding

Coded - Design and coding required

Number of Pages Required

5+ page

Font styles to use
Sans Serif

Colors
0592cd
33a6d7
85cae6
00a990
33b8a4
86cfc6
cee9f5
cfeae6
3277b5

Requirements
Must have
• *Should be able to switch from English to Chinese
Nice to have
• http://www.thebrightarchclinic.com/
• As a reference, the above link is the current website, but we would like to change the appearance and the content (our new logo's picture is attached)

```html
<!DOCTYPE html>
<html lang="en">
<head>
<meta charset="utf-8">
<title>The Bright Arch Clinic</title>
<link href="https://fonts.googleapis.com/css2?family=Lato:wght@400;700;900&display=swap" rel="stylesheet">
<style>
:root{
  --blue:#0592cd;
  --blue-mid:#33a6d7;
  --blue-soft:#85cae6;
  --sky:#cee9f5;
  --teal:#00a990;
  --teal-mid:#33b8a4;
  --navy:#3277b5;
  --ink:#111;
  --text:#555;
  --muted:#888;
  --footer:#2a2b2d;
  --white:#fff;
}
*{margin:0;padding:0;box-sizing:border-box}
html,body{width:1200px;height:4389px;overflow:hidden}
body{font-family:'Lato',sans-serif;color:var(--ink);background:var(--white);position:relative}
section,header,footer{position:absolute;left:0;width:1200px}
.abs{position:absolute}

/* header */
.site-header{top:0;height:75px;background:var(--sky);border-bottom:2px solid var(--blue-soft)}
.brand{left:162px;top:8px;display:flex;flex-direction:column;align-items:flex-start}
.brand-mark{width:34px;height:34px;background:var(--blue-mid);margin-left:24px}
.brand-name{font-size:11px;font-weight:700;color:var(--blue);margin-top:6px;letter-spacing:.2px}
.nav{left:420px;top:28px;display:flex;gap:22px;font-size:12px;color:#333}
.lang{left:978px;top:23px;width:60px;height:28px;border-radius:14px;background:var(--teal);color:#fff;font-size:11px;font-weight:700;display:flex;align-items:center;padding-left:10px;gap:14px}
.lang svg{width:9px}

/* hero */
.hero{top:75px;height:600px;background:linear-gradient(100deg,#4a4d50 0%,#5d6164 45%,#7e8285 70%,#9b9fa2 100%)}
.hero h1{left:162px;top:148px;font-size:46px;line-height:53px;font-weight:700;color:#fff;width:400px}
.hero p{left:162px;top:318px;font-size:11.5px;line-height:19px;color:#eee;width:400px}
.btn-contact{left:162px;top:380px;width:172px;height:48px;border-radius:24px;background:linear-gradient(90deg,var(--blue),var(--teal-mid));color:#fff;font-weight:700;font-size:17px;display:flex;align-items:center;padding-left:20px}
.btn-contact .arrow{position:absolute;right:6px;top:6px;width:36px;height:36px;border-radius:50%;background:#fff;display:flex;align-items:center;justify-content:center}

/* section heads */
.sec-head{left:0;width:1200px;text-align:center}
.sec-mark{display:block;width:46px;height:26px;background:var(--blue-mid);margin:0 auto 4px}
.sec-label{font-size:14px;color:var(--teal);font-weight:400}
.sec-title{font-size:36px;font-weight:900;color:var(--ink);margin-top:6px}

/* services */
.services{top:675px;height:672px}
.svc{width:205px;height:190px;background:#fff;border:1px solid #e3e3e3;box-shadow:0 0 6px rgba(0,0,0,.12);text-align:center;padding:20px 18px 0}
.svc-icon{width:60px;height:60px;border-radius:50%;background:var(--navy);margin:0 auto 14px;display:flex;align-items:center;justify-content:center}
.svc h3{font-size:14px;font-weight:900;margin-bottom:8px;white-space:nowrap}
.svc p{font-size:11px;line-height:19px;color:var(--muted)}

/* about */
.about{top:1347px;height:406px}
.about-copy{left:310px;top:140px;width:580px;text-align:center;font-size:11.5px;line-height:19.5px;color:var(--text)}
.about-copy p+p{margin-top:18px}
.btn-read{left:543px;top:312px;width:113px;height:38px;border-radius:19px;background:var(--teal);color:#fff;font-size:13px;font-weight:700;display:flex;align-items:center;justify-content:center}

/* patient info */
.patient{top:1753px;height:637px;background:linear-gradient(90deg,#eceff0,#e2e6e8 60%,#d8dde0)}
.patient-photo{left:735px;top:70px;width:440px;height:567px;background:linear-gradient(180deg,#c9d2d8,#eef2f5 55%,#dfe5ea);border-radius:200px 200px 0 0}
.info-box{width:448px;height:88px;background:#fff;border:1px solid #ddd;box-shadow:0 0 6px rgba(0,0,0,.1);padding:14px 16px}
.info-box h3{font-size:16px;font-weight:700;color:var(--blue);margin-bottom:8px}
.info-box p{font-size:11px;line-height:19px;color:#333}

/* team */
.team{top:2390px;height:508px}
.member{width:277px;top:188px;height:300px}
.member-photo{width:277px;height:211px;background:linear-gradient(180deg,#bfb8b0,#8e8680)}
.member-bar{height:89px;background:var(--blue);padding:22px 14px 0}
.member-bar h3{font-size:14px;font-weight:700;color:#fff;margin-bottom:10px}
.member-bar p{font-size:11px;color:var(--blue-soft)}

/* blog */
.blog{top:2898px;height:555px}
.post{width:428px;top:159px;height:324px;background:#fff;border:1px solid #ddd;box-shadow:0 0 6px rgba(0,0,0,.1)}
.post-photo{height:182px;background:linear-gradient(120deg,#d8dde2,#b9c2cc)}
.post-body{padding:12px 12px 0}
.post-body h3{font-size:13px;font-weight:900;margin-bottom:4px}
.post-date{font-size:9px;color:var(--blue);margin-bottom:8px}
.post-body p{font-size:11px;line-height:19px;color:var(--muted)}

/* testimonials */
.reviews{top:3453px;height:485px;background:linear-gradient(90deg,#eef0f1,#f6f7f8 50%,#eceeef)}
.avatar{left:556px;top:198px;width:88px;height:88px;border-radius:50%;border:4px solid var(--blue);background:linear-gradient(180deg,#cdd5dc,#8b96a0)}
.quote{font-size:56px;font-weight:900;color:var(--blue-soft);line-height:1}
.client{left:0;width:1200px;top:305px;text-align:center;font-size:12px;font-weight:700}
.review-text{left:390px;top:330px;width:420px;text-align:center;font-size:11px;line-height:19px;color:var(--text)}
.dots{left:548px;top:434px;display:flex;gap:18px}
.dots span{width:11px;height:11px;border-radius:50%;border:1px solid #333}
.dots span.on{background:radial-gradient(#333 30%,transparent 36%)}

/* cta band */
.cta{top:3938px;height:116px;background:var(--blue)}
.cta h2{left:162px;top:28px;font-size:26px;font-weight:900;color:#fff}
.cta p{left:162px;top:66px;width:380px;font-size:11px;line-height:19px;color:#fff}
.btn-book{left:866px;top:40px;width:172px;height:38px;border-radius:19px;background:#fff;color:var(--blue);font-size:13px;font-weight:700;display:flex;align-items:center;justify-content:center}

/* footer */
.site-footer{top:4054px;height:335px;background:var(--footer);color:#ccc}
.f-brand{left:162px;top:32px}
.f-brand .brand-mark{margin-left:18px;width:44px;height:38px}
.f-brand .brand-name{color:var(--blue-mid);font-size:12px}
.f-about{left:162px;top:100px;width:200px;font-size:11px;line-height:19px;color:#ddd}
.socials{left:162px;top:206px;display:flex;gap:9px}
.socials span{width:36px;height:36px;border-radius:50%;border:1.5px solid var(--blue-mid)}
.socials span.on{background:var(--blue-mid)}
.f-col h4{font-size:14px;font-weight:700;color:var(--blue-mid);margin-bottom:24px}
.f-col ul{list-style:none;font-size:11px;line-height:23px;color:#ddd}
.contact-row{display:flex;gap:12px;font-size:11px;line-height:16px;color:#fff;margin-bottom:18px;align-items:flex-start}
.contact-row svg{flex:none;width:18px;height:18px;fill:var(--blue-mid)}
.f-rule{left:0;top:296px;width:1200px;height:1px;background:#444}
.copy{left:0;width:1200px;top:308px;text-align:center;font-size:11px;color:#ccc}
.copy b{color:#fff;font-weight:700}
</style>
</head>
<body>

<header class="site-header">
  <div class="brand abs"><span class="brand-mark"></span><span class="brand-name">THE BRIGHT ARCH CLINIC</span></div>
  <nav class="nav abs"><span>Home</span><span>About Us</span><span>Services</span><span>Meet us</span><span>Patient Info</span><span>Cases&amp;Reviews</span><span>Blog</span><span>Contact</span></nav>
  <div class="lang abs">Eng <svg viewBox="0 0 10 6"><path d="M0 0h10L5 6z" fill="#fff"/></svg></div>
</header>

<section class="hero" role="img" aria-label="Dentist examining a smiling patient in the dental chair">
  <h1 class="abs">We will provide a full scope of dental care services</h1>
  <p class="abs">Lorem Ipsum is simply dummy text of the printing and typesetting industry. Lorem Ipsum has been the.</p>
  <div class="btn-contact abs">Contact Us<span class="arrow"><svg width="16" height="12" viewBox="0 0 16 12"><path d="M1 6h13M9 1l5 5-5 5" stroke="#0592cd" stroke-width="1.6" fill="none"/></svg></span></div>
</section>

<section class="services">
  <div class="sec-head abs" style="top:65px"><span class="sec-mark"></span><div class="sec-label">SERVICES</div><h2 class="sec-title">What We Provide</h2></div>

  <div class="svc abs" style="left:160px;top:206px"><div class="svc-icon"><svg width="30" height="30" viewBox="0 0 30 30"><path d="M8 4c3 0 4 2 7 2s4-2 7-2c4 0 5 4 4 8-1 5-2 8-3 13-1 2-3 2-3 0l-2-7c0-2-3-2-3 0l-2 7c0 2-2 2-3 0-1-5-2-8-3-13C3 8 4 4 8 4z" fill="none" stroke="#fff" stroke-width="1.8"/></svg></div><h3>Cleaning and Prevention</h3><p>Lorem Ipsum is simply dummy text of the printing and typesetting industry.</p></div>
  <div class="svc abs" style="left:385px;top:237px"><div class="svc-icon"><svg width="30" height="30" viewBox="0 0 30 30"><path d="M8 4c3 0 4 2 7 2s4-2 7-2c4 0 5 4 4 8-1 5-2 8-3 13-1 2-3 2-3 0l-2-7c0-2-3-2-3 0l-2 7c0 2-2 2-3 0-1-5-2-8-3-13C3 8 4 4 8 4z" fill="none" stroke="#fff" stroke-width="1.8"/></svg></div><h3>Cosmetic Dentistry</h3><p>Lorem Ipsum is simply dummy text of the printing and typesetting industry.</p></div>
  <div class="svc abs" style="left:610px;top:206px"><div class="svc-icon"><svg width="34" height="20" viewBox="0 0 34 20"><path d="M3 4h28v6c0 5-4 8-14 8S3 15 3 10z" fill="none" stroke="#fff" stroke-width="1.8"/><path d="M9 4v9M14 4v11M20 4v11M25 4v9" stroke="#fff" stroke-width="1.4"/></svg></div><h3>Implant Dentistry</h3><p>Lorem Ipsum is simply dummy text of the printing and typesetting industry.</p></div>
  <div class="svc abs" style="left:835px;top:237px"><div class="svc-icon"><svg width="34" height="20" viewBox="0 0 34 20"><rect x="3" y="3" width="28" height="14" rx="6" fill="none" stroke="#fff" stroke-width="1.8"/><path d="M9 3v14M14 3v14M20 3v14M25 3v14" stroke="#fff" stroke-width="1.4"/></svg></div><h3>Removable Dentures</h3><p>Lorem Ipsum is simply dummy text of the printing and typesetting industry.</p></div>

  <div class="svc abs" style="left:160px;top:418px"><div class="svc-icon"><svg width="22" height="34" viewBox="0 0 22 34"><path d="M3 3h16v7H3zM6 10h10l-2 20h-6z" fill="none" stroke="#fff" stroke-width="1.8"/><path d="M7 15h8M7 20h8M8 25h6" stroke="#fff" stroke-width="1.4"/></svg></div><h3>Orthodontics</h3><p>Lorem Ipsum is simply dummy text of the printing and typesetting industry.</p></div>
  <div class="svc abs" style="left:385px;top:447px"><div class="svc-icon"><svg width="34" height="20" viewBox="0 0 34 20"><path d="M3 4h28v6c0 5-4 8-14 8S3 15 3 10z" fill="none" stroke="#fff" stroke-width="1.8"/><path d="M3 9h28" stroke="#fff" stroke-width="1.4"/></svg></div><h3>Clear Aligners</h3><p>Lorem Ipsum is simply dummy text of the printing and typesetting industry.</p></div>
  <div class="svc abs" style="left:610px;top:418px"><div class="svc-icon"><svg width="30" height="32" viewBox="0 0 30 32"><path d="M4 28V14C4 7 9 3 15 3s11 4 11 11v14M10 28V15c0-3 2-6 5-6s5 3 5 6v13" fill="none" stroke="#fff" stroke-width="1.8"/></svg></div><h3>Pediatric Dentistry</h3><p>Lorem Ipsum is simply dummy text of the printing and typesetting industry.</p></div>
  <div class="svc abs" style="left:835px;top:447px"><div class="svc-icon"><svg width="34" height="24" viewBox="0 0 34 24"><path d="M3 5h28v5c0 7-6 11-14 11S3 17 3 10z" fill="none" stroke="#fff" stroke-width="1.8"/><path d="M3 12h28M10 5v14M17 5v16M24 5v14" stroke="#fff" stroke-width="1.4"/></svg></div><h3>Multi Specialty Treatment</h3><p>Lorem Ipsum is simply dummy text of the printing and typesetting industry.</p></div>
</section>

<section class="about">
  <div class="sec-head abs" style="top:20px"><span class="sec-mark"></span><div class="sec-label">ABOUT</div><h2 class="sec-title">Welcome To Bright Arch Clinic</h2></div>
  <div class="about-copy abs">
    <p>Welcome to The Bright Arch Clinic where we specialize in General and Cosmetic Dentistry, Dental Implants, Periodontics (Gum Surgery), Endodontics (Root Canal Treatment) and Reconstructive Dentistry for patients in Fairhaven, Linden Park, Millbrook, Ashford, Crestview, Oakridge, Westbury, Elmsdale and all other surrounding neighborhoods of Fairhaven.</p>
    <p>With Northfield and Castleton credentials that inspire confidence, we offer cosmetic dentistry, general dentistry and multi-specialty dental care all under one roof in our state-of-the-art cosmetic dental center.</p>
  </div>
  <div class="btn-read abs">Read More</div>
</section>

<section class="patient">
  <div class="patient-photo abs" role="img" aria-label="Smiling doctor in a white coat holding a clipboard"></div>
  <div class="sec-head abs" style="top:42px"><span class="sec-mark"></span><div class="sec-label">PATIENT INFO</div><h2 class="sec-title">Patient Details</h2></div>
  <div class="info-box abs" style="left:162px;top:179px"><h3>New Patient offer</h3><p>Lorem Ipsum is simply dummy text of the printing and typesetting industry. Lorem Ipsum has been the industry's standard dummy text ever since the 1500s.</p></div>
  <div class="info-box abs" style="left:200px;top:284px"><h3>Patient Portal</h3><p>Lorem Ipsum is simply dummy text of the printing and typesetting industry. Lorem Ipsum has been the industry's standard dummy text ever since the 1500s.</p></div>
  <div class="info-box abs" style="left:162px;top:390px"><h3>Accepted Insurance</h3><p>Lorem Ipsum is simply dummy text of the printing and typesetting industry. Lorem Ipsum has been the industry's standard dummy text ever since the 1500s.</p></div>
  <div class="info-box abs" style="left:200px;top:494px"><h3>Helpful Tips</h3><p>Lorem Ipsum is simply dummy text of the printing and typesetting industry. Lorem Ipsum has been the industry's standard dummy text ever since the 1500s.</p></div>
</section>

<section class="team">
  <div class="sec-head abs" style="top:62px"><span class="sec-mark"></span><div class="sec-label">OUR TEAM</div><h2 class="sec-title">MEET US</h2></div>
  <div class="member abs" style="left:162px"><div class="member-photo" role="img" aria-label="Portrait of an orthodontist"></div><div class="member-bar"><h3>LENA MORROW, DMD, MS</h3><p>Board Certified Orthodontist</p></div></div>
  <div class="member abs" style="left:462px"><div class="member-photo" role="img" aria-label="Portrait of a pediatric dentist"></div><div class="member-bar"><h3>VICTOR HALE, DMD</h3><p>Board Certified, Pediatric Dentist, Orthodontist</p></div></div>
  <div class="member abs" style="left:762px"><div class="member-photo" role="img" aria-label="Portrait of a general dentist"></div><div class="member-bar"><h3>DR. NADIA VEREL, DMD</h3><p>General Dentist</p></div></div>
</section>

<section class="blog">
  <div class="sec-head abs" style="top:30px"><span class="sec-mark"></span><div class="sec-label">BLOG</div><h2 class="sec-title">Latest Updates</h2></div>
  <article class="post abs" style="left:162px"><div class="post-photo" role="img" aria-label="Patient smiling during a dental check-up"></div><div class="post-body"><h3>Lorem Ipsum is simply dummy text of the printing and typesetting.</h3><div class="post-date">3 August 2019</div><p>Lorem Ipsum is simply dummy text of the printing and typesetting industry. Lorem Ipsum has been the industry's standard dummy text ever since the 1500s, when an unknown printer took a galley of type and scrambled it to make a type specimen book.</p></div></article>
  <article class="post abs" style="left:611px"><div class="post-photo" style="background:linear-gradient(120deg,#4b6584,#9aa9b8)" role="img" aria-label="Dentist treating a patient in a clinic"></div><div class="post-body"><h3>Lorem Ipsum is simply dummy text of the printing and typesetting.</h3><div class="post-date">3 August 2019</div><p>Lorem Ipsum is simply dummy text of the printing and typesetting industry. Lorem Ipsum has been the industry's standard dummy text ever since the 1500s, when an unknown printer took a galley of type and scrambled it to make a type specimen book.</p></div></article>
</section>

<section class="reviews" role="img" aria-label="Soft faded background of a dental treatment room">
  <div class="sec-head abs" style="top:58px"><span class="sec-mark"></span><div class="sec-label">CLIENTS REVIEW</div><h2 class="sec-title">Our Testimonials</h2></div>
  <div class="avatar abs" role="img" aria-label="Client portrait"></div>
  <div class="quote abs" style="left:346px;top:270px">&ldquo;</div>
  <div class="client abs">-Client Name</div>
  <p class="review-text abs">Lorem Ipsum is simply dummy text of the printing and typesetting industry. Lorem Ipsum has been the industry's standard dummy text ever since the 1500s, when an unknown printer took a galley of type and scrambled it to make a type specimen book.</p>
  <div class="quote abs" style="left:836px;top:366px">&rdquo;</div>
  <div class="dots abs"><span></span><span class="on"></span><span></span><span></span></div>
</section>

<section class="cta">
  <h2 class="abs">&ldquo;YOUR SMILE. OUR PASSION.&rdquo;</h2>
  <p class="abs">Thank you for your trust in us. We look forward to working with you towards a healthy and beautiful smile.</p>
  <div class="btn-book abs">Book An Appointment</div>
</section>

<footer class="site-footer">
  <div class="brand f-brand abs"><span class="brand-mark"></span><span class="brand-name">THE BRIGHT ARCH CLINIC</span></div>
  <p class="f-about abs">Lorem Ipsum is simply dummy text of the printing and typesetting industry. Lorem Ipsum has been the industry's standard dummy text ever since.</p>
  <div class="socials abs"><span></span><span></span><span class="on"></span><span></span></div>

  <div class="f-col abs" style="left:387px;top:40px"><h4>Quick Links</h4><ul><li>Home</li><li>About us</li><li>Services</li><li>Meet Us</li><li>Patient Info</li></ul></div>
  <div class="f-col abs" style="left:614px;top:40px"><h4>Sitemap</h4><ul><li>Blog</li><li>Client reviews</li><li>Terms &amp; Conditions</li><li>Support</li><li>Appointment</li><li>FAQ</li></ul></div>
  <div class="f-col abs" style="left:837px;top:40px"><h4>Contact Info</h4>
    <div class="contact-row"><svg viewBox="0 0 24 24"><path d="M6.6 10.8a15 15 0 0 0 6.6 6.6l2.2-2.2c.3-.3.7-.4 1-.2 1.1.4 2.3.6 3.6.6.6 0 1 .4 1 1V20c0 .6-.4 1-1 1A17 17 0 0 1 3 4c0-.6.4-1 1-1h3.5c.6 0 1 .4 1 1 0 1.3.2 2.5.6 3.6.1.3 0 .7-.2 1z"/></svg><b style="font-weight:700;line-height:18px">555.204.7781</b></div>
    <div class="contact-row"><svg viewBox="0 0 24 24"><path d="M12 2a7 7 0 0 0-7 7c0 5 7 13 7 13s7-8 7-13a7 7 0 0 0-7-7zm0 9.5A2.5 2.5 0 1 1 12 6.5a2.5 2.5 0 0 1 0 5z"/></svg><span>270 Linden Row, Suite 12,<br>Fairhaven MA 02719</span></div>
    <div class="contact-row"><svg viewBox="0 0 24 24"><path d="M2 5h20v14H2zm2 2v.5l8 5 8-5V7l-8 5z"/></svg><span>info@thebrightarchclinic.com</span></div>
  </div>
  <div class="f-rule abs"></div>
  <div class="copy abs">&copy; 2019. <b>The Bright Arch Clinic.</b> All Rights Reserved. Privacy Policy.</div>
</footer>

</body>
</html>
```